Harborlight Plans (03)

We're designing a website to sell Medicare Supplements. Attached is the script we want to say and general layout, but please use your best knowledge to make it better. This platform should be extremely user-friendly, but we want to make it look fun and approachable! Most Insurance/medicare websites are very boring, drab, simple but we want this one to be more personalized, fun and sexy (but again, still user-friendly since our target demographic is 65+).

This homepage should include a fun and inviting quiz, the script is in the attachment below. It should also include the blurbs about what medicare supplements plans are and why they should buy them. Feel free to play around with cool fonts and imagery, we want the site to be engaging!

Target Market(s)

seniors

Industry/Entity Type

Insurance

Number of Pages Required

1 page

Requirements
Must have
• Quiz, company name and tag line, script
Nice to have
• fun, engaging elements

```html
<!DOCTYPE html>
<html lang="en">
<head>
<meta charset="utf-8">
<title>Harborlight Plans – Medicare Supplement</title>
<link rel="stylesheet" href="https://fonts.googleapis.com/css2?family=Lato:ital,wght@0,300;0,400;0,700;0,900;1,400&family=Montserrat:wght@300;400;800&display=swap">
<style>
  :root{
    --red:#e8362f;
    --orange:#ef6a3a;
    --navy:#2e3548;
    --band-top:#3d4a64;
    --band-bottom:#2a3247;
    --footer:#2f3a52;
    --footer-bottom:#222a3b;
    --page:#f2f2f2;
    --white:#ffffff;
    --text:#6a6a6a;
    --ink:#2b2b2b;
    --cream:#fdf6ef;
  }
  *{box-sizing:border-box;margin:0;padding:0}
  html,body{width:1200px;height:3150px;overflow:hidden}
  body{position:relative;background:var(--page);font-family:'Lato',sans-serif;color:var(--text)}
  .abs{position:absolute}

  /* header */
  .site-header{left:0;top:0;width:1200px;height:88px;background:var(--white);border-top:4px solid var(--red);box-shadow:0 2px 6px rgba(0,0,0,.05);z-index:2}
  .brand{left:144px;top:24px;display:flex;align-items:center;gap:12px;font-family:'Montserrat',sans-serif;font-weight:400;font-size:29px;color:var(--ink)}
  .brand-dot{width:40px;height:40px;border-radius:50%;background:var(--orange)}
  .main-nav{left:571px;top:30px;display:flex;gap:19px;font-size:16px;color:#555}
  .main-nav .active{color:var(--ink);border-bottom:3px solid var(--red);padding-bottom:4px}
  .call{display:flex;align-items:center;gap:8px;font-weight:900;color:var(--ink);font-size:25px}
  .header-call{left:780px;top:24px}
  .phone-icon{width:38px;height:38px;flex:none}

  /* hero */
  .hero{left:0;top:88px;width:1200px;height:489px;background:linear-gradient(90deg,#f3ebe2 0%,var(--cream) 55%,#fff9f3 100%)}
  .hero-photo{left:0;top:0;width:600px;height:489px;background:linear-gradient(100deg,#a9907a 0%,#d8c3ae 45%,#efe3d6 80%,rgba(253,246,239,0) 100%)}
  .hero-title{left:577px;top:110px;font-family:'Montserrat',sans-serif;color:#1e1e1e;line-height:1}
  .hero-title .bold{display:block;font-weight:800;font-size:56px;letter-spacing:1px}
  .hero-title .light{display:block;font-weight:300;font-size:56px;margin-top:6px;letter-spacing:1px}
  .hero-tag{left:577px;top:250px;width:460px;font-size:19px;line-height:26px;color:#7a7a7a}
  .hero-call{left:577px;top:330px;font-size:24px;color:var(--red)}
  .hero-call small{font-size:19px;font-weight:400;color:var(--ink);margin-left:10px}

  /* intro band */
  .intro{left:0;top:577px;width:1200px;height:185px;background:linear-gradient(180deg,var(--band-top),var(--band-bottom));color:var(--white);text-align:center;font-size:20px;line-height:31px;padding-top:50px}

  /* quiz */
  .quiz{left:44px;top:823px;width:1112px;height:530px;background:var(--white);border-radius:4px}
  .quiz-title{left:0;top:62px;width:1112px;text-align:center;font-weight:900;font-size:24px;color:var(--navy)}
  .question{top:140px;display:flex}
  .question h3{font-weight:400;font-size:23px;color:var(--navy);white-space:nowrap}
  .options{list-style:none;font-size:16px;color:var(--ink)}
  .options li{display:flex;align-items:center;height:32px}
  .options li::before{content:"";width:14px;height:14px;border:2.5px solid var(--red);border-radius:50%;margin-right:18px}
  .divider{top:140px;width:1px;height:125px;background:#e3e3e3}
  .quiz-sub{left:0;top:323px;width:1112px;text-align:center;font-size:20px;color:#777;font-weight:300}
  .zip{left:294px;top:393px;width:328px;height:52px;background:var(--white);box-shadow:0 1px 6px rgba(0,0,0,.15);display:flex;align-items:center;padding-left:18px;gap:10px;font-size:13px;color:#666}
  .quote-btn{left:627px;top:393px;width:191px;height:52px;background:var(--red);color:var(--white);font-weight:900;font-size:16px;display:flex;align-items:center;justify-content:center}

  /* what is */
  .section-title{font-weight:900;font-size:24px;color:var(--navy);letter-spacing:-.3px}
  .what-title{left:0;top:1440px;width:1200px;text-align:center}
  .what-copy{left:158px;top:1503px;width:884px;text-align:center;font-size:15.5px;line-height:30.5px;color:#6c6c6c}
  .benefits{list-style:none;font-size:15.5px;line-height:25.5px;color:var(--ink)}
  .benefits li{display:flex;gap:10px}
  .tick{width:16px;height:16px;flex:none;margin-top:5px}

  /* costs */
  .costs-title{left:142px;top:1829px;line-height:34px}
  .costs-copy{left:142px;top:1917px;width:462px;font-size:16px;line-height:30.5px;color:#6c6c6c}
  .rates{left:142px;top:2128px;width:450px;list-style:none;font-size:16px;line-height:25.5px;color:var(--ink)}
  .rates li{display:flex;gap:10px;margin-bottom:20px}
  .rates span{max-width:418px}
  .rates b{color:var(--red);font-weight:700;font-size:19px}
  .costs-photo{left:651px;top:1931px;width:404px;height:511px;background:linear-gradient(160deg,#8a4a3a 0%,#c48b7a 35%,#d9b8d6 70%,#cdb1cf 100%)}
  .note{left:0;top:2508px;width:1200px;text-align:center;font-style:italic;font-size:22px;line-height:33px;color:var(--ink)}

  /* footer */
  .site-footer{left:0;top:2628px;width:1200px;height:436px;background:var(--footer);color:var(--white)}
  .footer-art{left:144px;top:50px;width:361px;height:337px;border-radius:12px;background:linear-gradient(135deg,#b77a3e 0%,#e3a15a 45%,#c98b6a 100%);opacity:.85}
  .footer-ask{left:566px;top:60px;font-size:19px;line-height:29px}
  .footer-call{left:780px;top:68px;color:var(--white)}
  .footer-head{font-weight:400;font-size:23px;color:var(--red)}
  .footer-links{list-style:none;font-size:12px;line-height:29.5px;letter-spacing:.2px}
  .float-btn{left:998px;top:2951px;width:202px;height:58px;background:var(--red);color:var(--white);border-radius:29px 0 0 29px;font-size:16px;display:flex;align-items:center;justify-content:center}
  .bottom-bar{left:0;top:3064px;width:1200px;height:86px;background:var(--footer-bottom);color:var(--white)}
  .copyright{left:144px;top:35px;font-size:12px}
  .social{left:894px;top:24px;display:flex;gap:8px}
  .social span{width:34px;height:34px;border:1.5px solid var(--white);border-radius:50%;display:block}
</style>
</head>
<body>

<header class="site-header abs">
  <div class="brand abs"><span class="brand-dot"></span>Harborlight Plans</div>
  <nav class="main-nav abs"><span class="active">Home</span><span>Quote</span><span>Blog</span></nav>
  <div class="call header-call abs">
    <svg class="phone-icon" viewBox="0 0 40 40"><circle cx="20" cy="20" r="18" fill="none" stroke="#e8362f" stroke-width="2.5"/><path d="M14 11c2 0 3 4 3 5s-2 2-2 3 3 6 6 7c1 0 2-2 3-2s5 1 5 3-2 3-3 3c-7 0-15-8-15-15 0-2 1-4 3-4z" fill="none" stroke="#e8362f" stroke-width="2"/></svg>
    CALL (800) 555-0142
  </div>
</header>

<section class="hero abs">
  <div class="hero-photo abs" role="img" aria-label="Smiling senior couple looking at a laptop while paying online"></div>
  <h1 class="hero-title abs"><span class="bold">HARBORLIGHT</span><span class="light">PLANS</span></h1>
  <p class="hero-tag abs">Be confident in choosing the Medicare Supplement plan that’s right for you.</p>
  <div class="call hero-call abs">
    <svg class="phone-icon" viewBox="0 0 40 40"><circle cx="20" cy="20" r="18" fill="none" stroke="#e8362f" stroke-width="2.5"/><path d="M14 11c2 0 3 4 3 5s-2 2-2 3 3 6 6 7c1 0 2-2 3-2s5 1 5 3-2 3-3 3c-7 0-15-8-15-15 0-2 1-4 3-4z" fill="none" stroke="#e8362f" stroke-width="2"/></svg>
    CALL (800) 555-0142 <small>to talk to a live agent.</small>
  </div>
</section>

<section class="intro abs">
  <p>We know insurance can be confusing. With so much information and not enough answers, we’re here<br>to help you find the plan that works best for you, your family and your health. Take this short quiz to to<br>find flexible and affordable plans that you can feel confident in.</p>
</section>

<section class="quiz abs">
  <h2 class="quiz-title abs">QUIZ SCRIPT</h2>
  <div class="question abs" style="left:32px"><h3 style="width:110px">1 ) I am</h3>
    <ul class="options"><li>Over 64 years old</li><li>64 years old</li><li>Under 64 years old</li></ul></div>
  <div class="divider abs" style="left:368px"></div>
  <div class="question abs" style="left:421px"><h3 style="width:111px">2 ) I am</h3>
    <ul class="options"><li>Male</li><li>Female</li><li>Unspecified</li></ul></div>
  <div class="divider abs" style="left:698px"></div>
  <div class="question abs" style="left:743px"><h3 style="width:199px">3 ) I want to see</h3>
    <ul class="options"><li>Free plans</li><li>Premium plans</li><li>All plans</li></ul></div>
  <p class="quiz-sub abs">Be confident choosing the Medicare Supplement plan that's right for you.</p>
  <div class="zip abs">
    <svg width="12" height="15" viewBox="0 0 12 16"><path d="M6 0a6 6 0 0 0-6 6c0 4 6 10 6 10s6-6 6-10a6 6 0 0 0-6-6z" fill="#ef6a3a"/><circle cx="6" cy="6" r="2.2" fill="#fff"/></svg>
    Enter Zipcode
  </div>
  <div class="quote-btn abs">GET FREE QUOTE</div>
</section>

<h2 class="section-title what-title abs">WHAT IS A MEDICARE SUPPLEMENT PLAN?</h2>
<p class="what-copy abs">Each Medicare Supplement insurance plan offers a different level of basic benefits, but each lettered plan will include the same standardized basic benefits regardless of insurance company and location. Medicare Supplement insurance plans do not always cover vision, dental, long-term care, or hearing aids, but all plans must cover at least a portion of the following basic benefits:</p>

<ul class="benefits abs" style="left:166px;top:1648px;width:420px">
  <li><svg class="tick" viewBox="0 0 16 16"><circle cx="8" cy="8" r="6.5" fill="none" stroke="#e8362f" stroke-width="2"/><path d="M5 8l2 2 4-4" fill="none" stroke="#e8362f" stroke-width="2"/></svg><span>Medicare Part A coinsurance costs up to an additional 365 days after Medicare benefits are exhausted</span></li>
  <li style="margin-top:28px"><svg class="tick" viewBox="0 0 16 16"><circle cx="8" cy="8" r="6.5" fill="none" stroke="#e8362f" stroke-width="2"/><path d="M5 8l2 2 4-4" fill="none" stroke="#e8362f" stroke-width="2"/></svg><span>Medicare Part B coinsurance or copayments</span></li>
</ul>
<ul class="benefits abs" style="left:641px;top:1648px;width:420px">
  <li><svg class="tick" viewBox="0 0 16 16"><circle cx="8" cy="8" r="6.5" fill="none" stroke="#e8362f" stroke-width="2"/><path d="M5 8l2 2 4-4" fill="none" stroke="#e8362f" stroke-width="2"/></svg><span>Medicare Part A hospice care coinsurance<br>or copayments</span></li>
  <li style="margin-top:28px"><svg class="tick" viewBox="0 0 16 16"><circle cx="8" cy="8" r="6.5" fill="none" stroke="#e8362f" stroke-width="2"/><path d="M5 8l2 2 4-4" fill="none" stroke="#e8362f" stroke-width="2"/></svg><span>First three pints of blood used in a medical procedure</span></li>
</ul>

<h2 class="section-title costs-title abs">MEDICARE SUPPLEMENT<br>INSURANCE PLAN COSTS</h2>
<p class="costs-copy abs">Although private insurance companies are required to offer the same basic benefits for each lettered plan, they do have the ability to charge different premiums. You might want to shop around to find a Medicare Supplement insurance plan that may fit your medical and financial needs. Insurance companies may price their plan premiums in any of the following ways:</p>

<ul class="rates abs">
  <li><svg class="tick" viewBox="0 0 16 16"><circle cx="8" cy="8" r="6.5" fill="none" stroke="#e8362f" stroke-width="2"/><path d="M5 8l2 2 4-4" fill="none" stroke="#e8362f" stroke-width="2"/></svg><span><b>Community no-age-rated:</b> These Medicare Supplement insurance plans charge premiums that are the same<br>across the board, regardless of age.</span></li>
  <li><svg class="tick" viewBox="0 0 16 16"><circle cx="8" cy="8" r="6.5" fill="none" stroke="#e8362f" stroke-width="2"/><path d="M5 8l2 2 4-4" fill="none" stroke="#e8362f" stroke-width="2"/></svg><span><b>Attained-age-rated:</b> Like issue-age-rated, these plans<br>base their premiums on the age you were when you<br>first bought a policy, but unlike issue-age-rated,<br>premiums increase as you get older.</span></li>
  <li><svg class="tick" viewBox="0 0 16 16"><circle cx="8" cy="8" r="6.5" fill="none" stroke="#e8362f" stroke-width="2"/><path d="M5 8l2 2 4-4" fill="none" stroke="#e8362f" stroke-width="2"/></svg><span><b>Issue-age-rated:</b> These plans base their premiums on<br>your age when you first enrolled in the policy. Therefore,<br>the younger you are when you enroll in this type<br>of plan, the lower your premium will be.</span></li>
</ul>
<div class="costs-photo abs" role="img" aria-label="Laughing senior woman in a striped top holding a teacup"></div>

<p class="note abs">Please note that no matter what rating method an insurance company uses, premiums<br>may increase over time for reasons other than age, such as inflation.</p>

<footer class="site-footer abs">
  <div class="footer-art abs" role="img" aria-label="Warm decorative photo collage of happy seniors"></div>
  <p class="footer-ask abs">Questions?<br>Speak with an Expert</p>
  <div class="call footer-call abs">
    <svg class="phone-icon" viewBox="0 0 40 40"><circle cx="20" cy="20" r="18" fill="none" stroke="#ef6a3a" stroke-width="2.5"/><path d="M14 11c2 0 3 4 3 5s-2 2-2 3 3 6 6 7c1 0 2-2 3-2s5 1 5 3-2 3-3 3c-7 0-15-8-15-15 0-2 1-4 3-4z" fill="none" stroke="#ef6a3a" stroke-width="2"/></svg>
    CALL (800) 555-0142
  </div>
  <div class="abs" style="left:566px;top:148px">
    <h3 class="footer-head">SITEMAP</h3>
    <ul class="footer-links" style="margin-top:8px"><li>HOME</li><li>ABOUT US</li><li>BLOG</li><li>MEDICARE PLANS</li><li>CONTACT US</li><li>AFFILIATE PROGRAM</li></ul>
  </div>
  <div class="abs" style="left:806px;top:148px">
    <h3 class="footer-head">INSURANCE QUOTES</h3>
    <ul class="footer-links" style="margin-top:8px"><li>HEALTH INSURANCE</li><li>LIFE INSURANCE</li><li>FINAL EXPENSE INSURANCE</li></ul>
  </div>
</footer>
<div class="float-btn abs">GET FREE QUOTES</div>

<div class="bottom-bar abs">
  <p class="copyright abs">Copyright © 2020 Harborlight Plans. All rights reserved &nbsp;|&nbsp; Privacy Policy &nbsp;|&nbsp; Terms and Use</p>
  <div class="social abs" aria-label="Social links"><span></span><span></span><span></span><span></span></div>
</div>

</body>
</html>
```